Advertising company unique advertising platform

we need a logo design for a new company based in Australia Melbourne. We develop innovated advertising platform where consumer can use this platform to get regular discount, as business owner they can use this platform for free advertisement. Payment for this advertisement platform only payable every two weeks, when I generate revenue for their business

Industry/Entity Type

Advertising

Contact Information for Business Card

Dale Morven | Co-Founder |Managing Director
Suite 718 240 Wattlebrook Lane Melbourne Vic 3000

ABN 38 614 207 923
Tel: +61 0487 259 318 | Email: dale.morven@plivorantu.com

Font styles to use
Decorative
Script

Requirements
Must have
• Try few different design and some round corner business card
Should not have
• One round corner business card...try 4 different colour background not only black, make sure two side is designed. Be creative so imagine you are giving this to a client make sure has wow factor, if you can also try one design with engrave like all the logo, words look 3d feel
• The word Advertising Platform use attached file font

```html
<!DOCTYPE html>
<html lang="en">
<head>
<meta charset="utf-8">
<title>Trellique Loop – Business Card</title>
<link href="https://fonts.googleapis.com/css2?family=Roboto:wght@400;500;700&display=swap" rel="stylesheet">
<style>
  :root {
    --stage: #3b3b3d;
    --card: #262626;
    --card-back: #1f1d1c;
    --pattern-a: #3a2a20;
    --pattern-b: #1e2a27;
    --brand: #f07a2c;
    --white: #ffffff;
    --warm-start: #f4c544;
    --warm-mid: #ee8a3c;
    --warm-end: #e4503a;
    --cool-start: #1de6b0;
    --cool-mid: #6fa3e0;
    --cool-end: #34a8ea;
    --icon-red: #e8413a;
  }
  * { box-sizing: border-box; margin: 0; padding: 0; }
  html, body {
    width: 1200px; height: 886px; overflow: hidden;
    background: var(--stage);
    font-family: "Roboto", Arial, sans-serif;
  }
  .stage {
    width: 1200px; height: 886px;
    display: flex; flex-direction: column; align-items: center; justify-content: center;
    gap: 50px;
  }
  .card {
    position: relative; width: 620px; height: 354px;
    border-radius: 6px; overflow: hidden;
    box-shadow: 0 14px 30px rgba(0,0,0,.45);
  }
  /* Back side */
  .card-back { background: var(--card-back); }
  .back-pattern {
    position: absolute; inset: 0;
    background: linear-gradient(135deg, var(--pattern-a), var(--pattern-b) 50%, var(--pattern-a));
    opacity: .8;
  }
  .back-brand {
    position: absolute; left: 390px; top: 140px;
    display: flex; flex-direction: column; align-items: center; gap: 10px;
  }
  .back-site { color: var(--white); font-size: 14px; letter-spacing: .3px; }

  /* Brand stand-in */
  .brand { display: flex; align-items: center; gap: 8px; }
  .brand-dot { width: 18px; height: 18px; border-radius: 50%; background: var(--brand); }
  .brand-name { color: var(--brand); font-weight: 700; font-size: 26px; letter-spacing: .5px; }

  /* Front side */
  .card-front { background: var(--card); }
  .front-brand { position: absolute; left: 300px; top: 62px; }
  .address {
    position: absolute; left: 200px; top: 150px;
    color: var(--white); font-size: 15px; line-height: 24px;
  }
  .address .line-1 { padding-left: 70px; }
  .band-title {
    position: absolute; left: 0; top: 200px; width: 350px; height: 95px;
    border-radius: 0 10px 10px 0;
    background: linear-gradient(90deg, var(--warm-start), var(--warm-mid) 50%, var(--warm-end));
    color: var(--white); text-align: right; padding: 10px 18px 0 0;
  }
  .person-name { font-weight: 700; font-size: 22px; line-height: 26px; }
  .person-role { font-size: 15px; line-height: 19px; font-weight: 500; }
  .band-contact {
    position: absolute; left: 362px; top: 262px; right: 0; height: 76px;
    border-radius: 10px 0 0 10px;
    background: linear-gradient(90deg, var(--cool-start), var(--cool-mid) 55%, var(--cool-end));
    color: var(--white); font-size: 15px; padding: 13px 0 0 22px;
  }
  .contact-row { display: flex; align-items: center; gap: 8px; line-height: 24px; }
  .contact-row svg { width: 13px; height: 13px; flex: none; }
</style>
</head>
<body>
<main class="stage">
  <section class="card card-back" aria-label="Card back">
    <div class="back-pattern" role="img" aria-label="Repeating brand pattern in dark brown and teal tones"></div>
    <div class="back-brand">
      <div class="brand"><span class="brand-dot"></span><span class="brand-name">Trellique Loop</span></div>
      <p class="back-site">plivorantu.com</p>
    </div>
  </section>

  <section class="card card-front" aria-label="Card front">
    <div class="front-brand brand"><span class="brand-dot"></span><span class="brand-name">Trellique Loop</span></div>
    <div class="address">
      <p class="line-1">Plivorantu, ABN 38 614 207 923</p>
      <p class="line-2">Suite 718 240 Wattlebrook Lane, Melbourne Vic 3000</p>
    </div>
    <div class="band-title">
      <p class="person-name">DALE MORVEN</p>
      <p class="person-role">CO-FOUNDER</p>
      <p class="person-role">MANAGING DIRECTOR</p>
    </div>
    <div class="band-contact">
      <p class="contact-row">
        <svg viewBox="0 0 24 24" aria-hidden="true"><path fill="var(--icon-red)" d="M6.6 10.8a15.1 15.1 0 0 0 6.6 6.6l2.2-2.2c.3-.3.7-.4 1-.2 1.1.4 2.3.6 3.6.6.6 0 1 .4 1 1V20c0 .6-.4 1-1 1A17 17 0 0 1 3 4c0-.6.4-1 1-1h3.5c.6 0 1 .4 1 1 0 1.3.2 2.5.6 3.6.1.3 0 .7-.2 1z"/></svg>
        +61 0487 259 318
      </p>
      <p class="contact-row">
        <svg viewBox="0 0 24 24" aria-hidden="true"><rect x="2" y="5" width="20" height="14" rx="2" fill="var(--icon-red)"/><path d="M3 6l9 7 9-7" stroke="var(--white)" stroke-width="1.6" fill="none"/></svg>
        dale.morven@plivorantu.com
      </p>
    </div>
  </section>
</main>
</body>
</html>
```